Business Card Design for a Personal Trainer

I need a business card design for my job as a personal trainer. It should have a unique, modern and exclusive design. On the front there should be only my logo with my name and my job. 0162/3819204 Tobias Lendhart Wiesengrundweg 14 80417 Munich Germany The most important contact information is the web adress. it can be bigger than the rest, but its not necessary. The card should be 8,5cmx5,5cm big. Font: Roboto. Colors: black, white, gray, 56c1ff.

```html
<!DOCTYPE html>
<html lang="de">
<head>
<meta charset="utf-8">
<title>Tobias Lendhart – Personal Trainer</title>
<link rel="stylesheet" href="https://fonts.googleapis.com/css2?family=Roboto:wght@300;400&display=swap">
<style>
  :root {
    --accent: #56c1ff;
    --text-gray: #c9cdd1;
    --label-gray: #b4b9bd;
    --bg-center: #1c3547;
    --bg-mid: #10202c;
    --bg-edge: #04080b;
    --photo-light: #6a6d70;
    --photo-dark: #1e2124;
  }
  html, body {
    margin: 0;
    padding: 0;
    width: 1200px;
    height: 777px;
    overflow: hidden;
    background: #000;
  }
  .card {
    position: relative;
    width: 1200px;
    height: 777px;
    overflow: hidden;
    font-family: "Roboto", Arial, sans-serif;
    background:
      radial-gradient(ellipse 70% 75% at 55% 45%, var(--bg-center) 0%, var(--bg-mid) 55%, var(--bg-edge) 100%);
  }
  .portrait {
    position: absolute;
    left: 90px;
    top: 78px;
    width: 412px;
    height: 699px;
  }
  .divider {
    position: absolute;
    left: 595px;
    top: 205px;
    width: 7px;
    height: 364px;
    background: var(--accent);
  }
  .line {
    position: absolute;
    left: 698px;
    margin: 0;
    line-height: 1;
    white-space: nowrap;
  }
  .name {
    top: 227px;
    font-size: 48px;
    font-weight: 400;
    color: var(--accent);
  }
  .role {
    top: 274px;
    left: 700px;
    font-size: 21px;
    font-weight: 400;
    color: var(--label-gray);
  }
  .phone {
    top: 330px;
    font-size: 48px;
    font-weight: 400;
    color: var(--accent);
    letter-spacing: 0.5px;
  }
  .address, .online {
    font-size: 32px;
    font-weight: 400;
    color: var(--text-gray);
  }
  .address-street { top: 387px; }
  .address-city { top: 432px; }
  .online-email { top: 487px; font-size: 31px; }
  .online-web { top: 524px; font-size: 31px; }
</style>
</head>
<body>
  <div class="card">
    <svg class="portrait" viewBox="0 0 412 699" role="img" aria-label="Black and white portrait photo of the trainer, arms crossed, wearing a dark long-sleeve shirt">
      <defs>
        <radialGradient id="portraitTone" cx="50%" cy="40%" r="65%">
          <stop offset="0%" stop-color="var(--photo-light)"/>
          <stop offset="100%" stop-color="var(--photo-dark)"/>
        </radialGradient>
      </defs>
      <rect x="0" y="0" width="412" height="699" fill="url(#portraitTone)"/>
    </svg>

    <div class="divider"></div>

    <p class="line name">Tobias Lendhart</p>
    <p class="line role">Personal Trainer</p>
    <p class="line phone">0162 3819 - 204</p>
    <p class="line address address-street">Wiesengrundweg 14</p>
    <p class="line address address-city">80417 München</p>
    <p class="line online online-email">kontakt@lendhart-training.de</p>
    <p class="line online online-web">www.lendhart-training.de</p>
  </div>
</body>
</html>
```